Australian Based Web Development Company Needs a Fresh New Modern Look (logo and responsive website)

We are Coral Web Development, an Australian based web development company looking to give our company a fresh, new and modern look.

We tend to deal with small to medium sized businesses, and want to convey the message that we are professional and capable of developing a solution to any need or problem.

Our specialty is custom development applications, such as, intranets, integration software, and client portals.

We have recently started mobile application development as well (iOS and Android).

You can view our current logo and website on https://www.coralwebdevelopment.example/

As we are looking for both a logo and a website design, we may decide to have the website design completed by a different designer to the winning logo designer.

Target Market(s)

Small to medium enterprise businesses

Industry/Entity Type

It Company

Logo Text

Coral Web Development

Number of Pages Required

2 page

Logo styles of interest
Abstract Logo
Wordmark Logo
Font styles to use
Sans Serif

Colors
85cae6
33b8a4

Requirements
Must have
• Website design - a responsive layout (960-1000px content width), and background image/texture of 2,560px wide. A home page design, and a generic content page design.
• Colours - we like blues, greens (more blue-green like teal) and grey, but we are open to seeing other colours if you feel appropriate.
Nice to have
• Website design - Two websites I like the design style is http://www.mavonstack.example/ and https://www.pilvo.example/au/accounting-software/

```html
<!DOCTYPE html>
<html lang="en">
<head>
<meta charset="utf-8">
<title>Newsletter Signup</title>
<link rel="stylesheet" href="https://fonts.googleapis.com/css2?family=Open+Sans:wght@300;400;600;700&display=swap">
<style>
  :root {
    --canvas-bg: #e9ecef;
    --page-white: #ffffff;
    --newsletter-top: #a3aaa9;
    --newsletter-mid: #6b7584;
    --newsletter-bottom: #3d4b68;
    --heading-light: #ffffff;
    --body-light: rgba(255, 255, 255, 0.78);
    --field-bg: #ffffff;
    --field-text: #b9bec6;
    --sky: #85cae6;
    --teal: #33b8a4;
    --ink: #3a3f47;
    --ink-soft: #8a9099;
    --outline: #c9cdd2;
  }
  * { box-sizing: border-box; margin: 0; padding: 0; }
  html, body {
    width: 1200px;
    height: 804px;
    overflow: hidden;
  }
  body {
    background: var(--canvas-bg);
    font-family: "Open Sans", sans-serif;
    display: flex;
    justify-content: center;
  }
  .mobile-page {
    width: 510px;
    height: 804px;
    display: flex;
    flex-direction: column;
    background: var(--page-white);
  }
  .intro-strip {
    height: 152px;
    display: flex;
    justify-content: center;
    padding-top: 30px;
  }
  .btn-outline {
    width: 146px;
    height: 54px;
    border: 2px solid var(--outline);
    border-radius: 4px;
    display: flex;
    align-items: center;
    justify-content: center;
    font-size: 12px;
    letter-spacing: 0.5px;
    text-transform: uppercase;
    color: var(--ink-soft);
  }
  .newsletter {
    height: 531px;
    background: linear-gradient(170deg, var(--newsletter-top) 0%, var(--newsletter-mid) 38%, var(--newsletter-bottom) 62%, var(--newsletter-bottom) 100%);
    text-align: center;
    padding-top: 30px;
  }
  .newsletter-title {
    font-size: 25px;
    font-weight: 400;
    line-height: 28px;
    color: var(--heading-light);
  }
  .newsletter-title strong { font-weight: 700; }
  .newsletter-intro {
    margin: 14px auto 0;
    width: 420px;
    font-size: 11px;
    line-height: 29px;
    color: var(--body-light);
  }
  .signup-form {
    margin-top: 22px;
    display: flex;
    flex-direction: column;
    align-items: center;
  }
  .field {
    width: 200px;
    height: 36px;
    margin-bottom: 19px;
    background: var(--field-bg);
    border-radius: 2px;
    padding-left: 12px;
    display: flex;
    align-items: center;
    font-size: 10px;
    color: var(--field-text);
  }
  .btn-solid {
    width: 134px;
    height: 46px;
    border-radius: 2px;
    display: flex;
    align-items: center;
    justify-content: center;
    font-size: 10px;
    font-weight: 600;
    letter-spacing: 0.6px;
    text-transform: uppercase;
    color: #ffffff;
  }
  .btn-submit { background: var(--sky); margin-top: 4px; }
  .btn-clear { background: var(--teal); margin-top: 8px; height: 42px; }
  .news-strip {
    flex: 1;
    display: flex;
    justify-content: center;
    padding-top: 22px;
  }
  .news-title {
    font-size: 26px;
    font-weight: 400;
    color: var(--ink);
  }
  .news-title strong { font-weight: 700; }
</style>
</head>
<body>
  <main class="mobile-page">
    <section class="intro-strip">
      <span class="btn-outline">Learn More</span>
    </section>

    <section class="newsletter">
      <h2 class="newsletter-title">For latest update <strong>join us</strong><br>our Newsletter</h2>
      <p class="newsletter-intro">Contrary to popular belief, Lorem Ipsum is not simply random text.<br>It has roots in a piece of classical Latin literature from 45 BC,<br>making it over 2000 years old.</p>
      <div class="signup-form">
        <span class="field">Name</span>
        <span class="field">Email</span>
        <span class="field">Country/City</span>
        <span class="btn-solid btn-submit">Submit</span>
        <span class="btn-solid btn-clear">Clear</span>
      </div>
    </section>

    <section class="news-strip">
      <h2 class="news-title"><strong>News &amp;</strong> Events</h2>
    </section>
  </main>
</body>
</html>
```